Consulting business card

*1) An Overview:* The business is simply a financial transaction wherein I
offer to provide advice to financial holders of commercial real estate
mortgages (which are sub-performing or non-performing), and said holders
are desirous of selling said mortgages which I will offer advice to said
holders in the purchase of said mortgages. Please note the attached copy
of a proposed line-by-line business card which starts with the 1st line
"RKW Advisory, LLC" with the 2nd line "Purchase of Commercial Mortgage
Loan" and the 3rd line "Sub-performing and Non-performing" is my desired
copy subject to any suggested changes. Please ignore the the copy below
the aforementioned proposed card/copy as it will be activated at a later
date.and advise
*2) The Target Market:* I contact and advise senior officers in banks,
insurance companies, and financial institutions such as CEOs, CFOs, COOs,
and Loan Mitigation Officers: the senior officers are tasked with the
removal of sub-performing and non-performing commercial real estate loans
from their real estate portfolios. The desired market is targeted at $1-10
million USD and located in the US.
*3) Design Specifics: *STYLE should be conservative and be representative
of the financial market contacts; COLOR might show a rich forest green
element, a gold foil accent, and subtle black printing, however,
alternatively, silver foil accent(s) with strong black print would seem in
harmony with the services offered, however, I would appreciate any artful
suggestions; IMAGERY should be subtle (no logo can be strong enough to make
an immediate impact): the quality should make the recipient feel he/she has
just met an experienced and competent financial adviser (I have over 55
years of successful financial and business experience).
720.217.6154davidfredrickjones@gmail.com

```html
<!DOCTYPE html>
<html lang="en">
<head>
<meta charset="utf-8">
<title>RKW Advisory, LLC — Business Card</title>
<link rel="stylesheet" href="https://fonts.googleapis.com/css2?family=Cutive+Mono&family=Tinos&family=Open+Sans:wght@400&display=swap">
<style>
  :root {
    --forest: #0b4c0b;
    --leaf: #2f6212;
    --card: #ededed;
    --ink: #1c1c1c;
    --rule: #3a3a3a;
    --backdrop: #d9d6cf;
  }
  * { margin: 0; padding: 0; box-sizing: border-box; }
  html, body { width: 1200px; height: 892px; overflow: hidden; background: var(--backdrop); }
  .business-card {
    position: absolute; left: 75px; top: 146px;
    width: 1050px; height: 600px;
    background: var(--card);
    overflow: hidden;
    box-shadow: 0 6px 18px rgba(0,0,0,.18);
  }
  .company-name {
    position: absolute; left: 80px; top: 78px;
    font-family: 'Cutive Mono', 'Courier New', monospace;
    font-size: 64px; letter-spacing: 2px;
    color: var(--forest); font-weight: 400;
  }
  .tagline {
    position: absolute; left: 158px; top: 172px;
    font-family: 'Tinos', 'Times New Roman', serif;
    font-size: 27px; line-height: 36px; color: var(--ink);
  }
  .tagline span { display: block; }
  .tagline .second { padding-left: 40px; }
  .person-name {
    position: absolute; left: 170px; top: 300px;
    font-family: 'Tinos', 'Times New Roman', serif;
    font-size: 50px; color: var(--forest);
  }
  .divider {
    position: absolute; left: 460px; top: 268px;
    width: 1.5px; height: 120px; background: var(--rule);
  }
  .contact-list {
    position: absolute; left: 530px; top: 278px;
    list-style: none;
    font-family: 'Open Sans', Verdana, sans-serif;
    font-size: 24px; color: var(--ink);
  }
  .contact-list li { display: flex; align-items: center; gap: 18px; height: 44px; }
  .contact-list svg { width: 22px; height: 20px; flex: none; }
  .swoosh { position: absolute; left: 0; bottom: 0; width: 1050px; height: 170px; }
</style>
</head>
<body>
  <div class="business-card">
    <h1 class="company-name">RKW Advisory LLC</h1>
    <p class="tagline">
      <span>Purchase of Commercial Mortgage Loan</span>
      <span class="second">Sub-performing and Non-performing</span>
    </p>
    <p class="person-name">Mark Ellison</p>
    <div class="divider"></div>
    <ul class="contact-list">
      <li>
        <svg viewBox="0 0 22 20" aria-hidden="true">
          <rect width="22" height="20" fill="var(--forest)"/>
          <path d="M7 4 L9 4 L10 7 L8.5 8 Q10 11 13 12.5 L14 11 L17 12 L17 14 Q16 16 14 16 Q6 14 5 6 Q5 4 7 4 Z" fill="#fff"/>
        </svg>
        555.304.8827
      </li>
      <li>
        <svg viewBox="0 0 22 20" aria-hidden="true">
          <rect width="22" height="20" fill="var(--forest)"/>
          <rect x="4" y="5" width="14" height="10" fill="none" stroke="#fff" stroke-width="1.5"/>
          <path d="M4 5 L11 11 L18 5" fill="none" stroke="#fff" stroke-width="1.5"/>
        </svg>
        tomasheraldwick@mailbox.example
      </li>
    </ul>
    <svg class="swoosh" viewBox="0 0 1050 170" preserveAspectRatio="none" aria-hidden="true">
      <path d="M0 170 L0 118 Q480 -10 1050 55 L1050 170 Z" fill="var(--forest)"/>
      <path d="M0 105 Q480 -35 1050 28 L1050 40 Q480 -18 0 108 Z" fill="var(--leaf)"/>
    </svg>
  </div>
</body>
</html>
```